Gestaltung von Honigetiketten
Zielgruppe
Ich bin ein Imker, der im eigenen Restaurant seinen Honig ausstellen und verkaufen möchte.
Aufgabenstellung
Ich möchte exklusive und edle Honigetiketten die auffallen. Bevorzugt mit den Farben Gold und Schwarz, siehe meinem bisher gesehenen Favoriten im Anhang.
Nur das Logo selbst (Baum) soll übernommen werden Farbe kann variieren, ebenso die Schrift ist variabel.
Auf die Vorderseite des Honigetiketts soll zu lesen sein:
- Deutscher Honig
- Sommertracht
- 500g
- Logo und Name
Auf der Rückseite des Honigetiketts soll zu finden sein:
- freies Feld für Stempel für Namen und Adresse des Abfüllers
- freies Feld für das Mindesthaltbarkeitsdatum

```html
<!DOCTYPE html>
<html lang="de">
<head>
<meta charset="utf-8">
<title>Honigetikett Sommertracht</title>
<link rel="stylesheet" href="https://fonts.googleapis.com/css2?family=Great+Vibes&family=Josefin+Sans:wght@300&family=PT+Sans+Narrow&display=swap">
<style>
  :root {
    --ink: #000000;
    --paper: #ffffff;
    --gold-dark: #a8842c;
    --gold-mid: #d8bd6a;
    --gold-light: #f3e6b0;
  }
  html, body {
    margin: 0;
    padding: 0;
    width: 1006px;
    height: 1200px;
    overflow: hidden;
    background: var(--paper);
  }
  .label {
    display: block;
    width: 1006px;
    height: 1200px;
  }
  .brand-name {
    font-family: "Josefin Sans", sans-serif;
    font-weight: 300;
    font-size: 60px;
    letter-spacing: 6px;
    fill: var(--gold-mid);
  }
  .brand-dot {
    fill: var(--gold-mid);
  }
  .address {
    font-family: "PT Sans Narrow", sans-serif;
    font-size: 34px;
    fill: var(--ink);
  }
  .variety {
    font-family: "Great Vibes", cursive;
    font-size: 140px;
    fill: var(--ink);
  }
  .product-type {
    font-family: "Josefin Sans", sans-serif;
    font-weight: 300;
    font-size: 42px;
    letter-spacing: 1px;
    fill: var(--ink);
  }
</style>
</head>
<body>
<svg class="label" viewBox="0 0 1535 1845" preserveAspectRatio="none" xmlns="http://www.w3.org/2000/svg">
  <defs>
    <linearGradient id="gold" x1="0" y1="0" x2="1" y2="0">
      <stop offset="0" stop-color="var(--gold-dark)"/>
      <stop offset="0.35" stop-color="var(--gold-light)"/>
      <stop offset="0.65" stop-color="var(--gold-mid)"/>
      <stop offset="1" stop-color="var(--gold-dark)"/>
    </linearGradient>
  </defs>

  <!-- neck strip -->
  <rect class="neck-strip" x="576" y="0" width="354" height="1185" fill="var(--ink)"/>

  <!-- gold rule above band -->
  <polygon class="band-rule" points="0,1186 1535,1174 1535,1184 0,1196" fill="url(#gold)"/>

  <!-- main black band with chevron bottom -->
  <polygon class="main-band" points="0,1198 1535,1186 1535,1432 758,1618 0,1432" fill="var(--ink)"/>

  <!-- gold chevron edge -->
  <polyline class="chevron-gold" points="0,1438 758,1624 1535,1438" fill="none" stroke="url(#gold)" stroke-width="8"/>

  <!-- black chevron stripes -->
  <polyline class="chevron-stripe" points="0,1458 758,1640 1535,1458" fill="none" stroke="var(--ink)" stroke-width="8"/>
  <polyline class="chevron-stripe" points="0,1474 758,1656 1535,1474" fill="none" stroke="var(--ink)" stroke-width="8"/>

  <!-- blank field for best-before date -->
  <polygon class="date-field" points="6,1362 271,1362 271,1492 6,1427" fill="var(--paper)"/>

  <!-- bottler address field -->
  <polygon class="address-field" points="1221,1202 1535,1202 1535,1420 1221,1496" fill="var(--paper)"/>
  <text class="address" x="1231" y="1260">
    <tspan x="1231" dy="0">Gasthaus</tspan>
    <tspan x="1231" dy="46">Brunnhof am Mühlbach</tspan>
    <tspan x="1231" dy="46">Birkenweiler Str. 14</tspan>
    <tspan x="1231" dy="46">90000 Talbach-Weiden</tspan>
  </text>

  <!-- brand name -->
  <circle class="brand-dot" cx="618" cy="1388" r="9"/>
  <text class="brand-name" x="645" y="1409">Brunnhof</text>

  <!-- product naming -->
  <text class="variety" x="760" y="1740" text-anchor="middle">Sommertracht</text>
  <text class="product-type" x="752" y="1798" text-anchor="middle">Deutscher Bienenhonig</text>
</svg>
</body>
</html>
```